Lumo Organic Baby Wipes for retail sales into supermarkets

Design a new Organic Baby Wipes Pack that has a similar feel and details to the attachments under the Brand Name LUMO Organics. Please keep all writing in English and highlight the following info on the Pack. - 80 Pack, 100% Biodegradable,
Aloe Vera, Chamomile,Natural Vitamin E to soothe baby's skin.
Hypo Allergenic, pH Balanced for baby's skin.
Fragrance Free, Alcohol Free, Chlorine Free, Parabens Free.

Target Market(s)

Mums looking for a Organic Baby Wipe

Industry/Entity Type

Baby

Font styles to use
Sans Serif

Colors
9bcb3c
abd036
cadf82
ffffff

Requirements
Must have
• Lumo Organics, White Base, majority green writing with different shades, touches of Brown to represent Bamboo Wipes.
• Please make ORGANIC writing very big.
Nice to have
• Natural Organic feel going to use matt packaging.
Should not have
• Cluttered too much information

```html
<!DOCTYPE html>
<html lang="en">
<head>
<meta charset="utf-8">
<title>Lumo Organic Baby Wipes – Pack Front</title>
<link rel="stylesheet" href="https://fonts.googleapis.com/css2?family=Alfa+Slab+One&family=Roboto+Condensed:wght@400;700&display=swap">
<style>
  :root {
    --bg: #e6f4da;
    --pack-white: #ffffff;
    --pack-cream: #eef0dc;
    --seal: #e4e7cc;
    --seal-line: #c9cea6;
    --leaf: #9bcb3c;
    --lime: #abd036;
    --pale-lime: #cadf82;
    --brand-green: #7cb342;
    --deep-green: #3f6b24;
    --bark: #8a5a1f;
    --ink: #2d3320;
    --photo-light: #f3dccb;
    --photo-mid: #e9bfa4;
    --photo-warm: #c98a5e;
  }
  * { margin: 0; padding: 0; box-sizing: border-box; }
  html, body { width: 1200px; height: 1042px; overflow: hidden; }
  body { background: var(--bg); position: relative; font-family: "Roboto Condensed", sans-serif; }

  .pack {
    position: absolute; left: 88px; top: 316px; width: 1004px; height: 480px;
    background: linear-gradient(180deg, var(--pack-cream) 0%, var(--pack-white) 14%, var(--pack-white) 84%, var(--pack-cream) 100%);
    overflow: hidden;
  }
  .pack__seal {
    position: absolute; top: 0; width: 42px; height: 100%; z-index: 3;
    background: repeating-linear-gradient(90deg, var(--seal) 0 5px, var(--seal-line) 5px 7px);
  }
  .pack__seal--left { left: 0; }
  .pack__seal--right { right: 0; }

  .photo {
    position: absolute; left: 456px; top: 16px; width: 548px; height: 436px;
    background: radial-gradient(ellipse at 45% 40%, var(--photo-light) 0%, var(--photo-mid) 55%, var(--photo-warm) 100%);
    border-radius: 40% 0 0 30%;
  }

  .brand {
    position: absolute; left: 146px; top: 58px;
    font-family: "Alfa Slab One", serif; font-size: 60px; line-height: 1;
    color: var(--brand-green);
  }
  .brand__tm { font-size: 14px; vertical-align: top; margin-left: 4px; }
  .title-organic {
    position: absolute; left: 82px; top: 154px;
    font-family: "Alfa Slab One", serif; font-weight: 400; font-size: 54px; letter-spacing: 1px; line-height: 1;
    color: var(--bark);
  }
  .title-product {
    position: absolute; left: 90px; top: 214px;
    font-family: "Alfa Slab One", serif; font-weight: 400; font-size: 45px; line-height: 1;
    color: var(--deep-green);
  }

  .benefits {
    position: absolute; left: 0; top: 278px; width: 410px; height: 132px;
    background: linear-gradient(90deg, var(--lime) 0%, var(--leaf) 55%, var(--pale-lime) 85%, rgba(255,255,255,0) 100%);
    padding: 6px 0 0 78px;
    font-size: 17.5px; line-height: 24.5px; color: var(--ink);
  }

  .count-badge { position: absolute; left: 428px; top: 90px; width: 110px; height: 120px; }

  .origin-seal {
    position: absolute; left: 390px; top: 322px; width: 78px; height: 78px;
    border: 2px solid var(--brand-green); border-radius: 50%;
  }

  .tagline {
    position: absolute; left: 696px; top: 410px; width: 308px; height: 46px;
    background: linear-gradient(90deg, rgba(155,203,60,0.6) 0%, var(--leaf) 20%, var(--brand-green) 100%);
    color: var(--pack-white); font-size: 22px; line-height: 46px; padding-left: 86px;
  }
</style>
</head>
<body>
  <main class="pack">
    <div class="pack__seal pack__seal--left"></div>
    <div class="pack__seal pack__seal--right"></div>

    <div class="photo" role="img" aria-label="Photograph of a smiling baby held cheek to cheek by its mother"></div>

    <div class="brand">Lumo<span class="brand__tm">™</span></div>
    <h1 class="title-organic">ORGANIC</h1>
    <h2 class="title-product">Baby Wipes</h2>

    <p class="benefits">
      Aloe Vera, Chamomile, Natural Vitamin E<br>
      to soothe baby's skin, Hypo Allergenic,<br>
      PH Balanced for baby's skin.<br>
      Fragrance Free, Alcohol Free,<br>
      Chlorine Free, Parabens Free.
    </p>

    <svg class="count-badge" viewBox="0 0 110 120" aria-label="80 Pack, 100% Biodegradable">
      <defs>
        <path id="count-arc" d="M12 44 Q55 4 100 44"/>
      </defs>
      <text font-family="Alfa Slab One, serif" font-size="20" fill="#3f6b24">
        <textPath href="#count-arc" startOffset="50%" text-anchor="middle">80 ★ Pack</textPath>
      </text>
      <polygon points="55,36 96,58 96,100 55,122 14,100 14,58" fill="#9bcb3c" transform="translate(0,-6)"/>
      <text x="55" y="80" text-anchor="middle" font-family="Roboto Condensed, sans-serif" font-weight="700" font-size="26" fill="#ffffff">100%</text>
      <text x="55" y="96" text-anchor="middle" font-family="Roboto Condensed, sans-serif" font-weight="700" font-size="11" fill="#ffffff">Biodegradable</text>
    </svg>

    <div class="origin-seal"></div>

    <div class="tagline">Gentle By Nature</div>
  </main>
</body>
</html>
```